Catalogue Design Project

We need a catalog design for a new private university called Redwell Institute Bayshore (see website www.rwi-bs.org). The catalog should be about 30 pages maximum and will include items such as General Information, Academic schedule, department descriptions, program descriptions, course descriptions, school policies, student services, admissions, San diego Lifestyle, etc.
I will provide the text but I need a professional design with regard to page layouts. I have provided some examples.
Ok, i posted the catalog content, just missing course descriptions.
Target Market(s)
Young Professionals, Foreign Students
Industry/Entity Type
University
Look and feel
Each slider illustrates characteristics of the customer's brand and the style your logo design should communicate.

```html
<!DOCTYPE html>
<html lang="en">
<head>
<meta charset="utf-8">
<title>Redwell Institute Bayshore — Catalogue Page 2</title>
<link href="https://fonts.googleapis.com/css2?family=Archivo+Black&family=Carlito:wght@400;700&family=Cinzel:wght@400&display=swap" rel="stylesheet">
<style>
  :root {
    --paper: #ffffff;
    --ink: #111111;
    --muted: #8a8a8a;
    --caption: #333333;
    --dagger: #8b1a1a;
    --rule: #7ea0c4;
    --brand: #2a47a8;
    --photo-campus-a: #9c9f86;
    --photo-campus-b: #d9ddd2;
    --photo-city-a: #c9d2d9;
    --photo-city-b: #7f8d99;
    --photo-street-a: #6f7a58;
    --photo-street-b: #9a5a4a;
  }
  * { margin: 0; padding: 0; box-sizing: border-box; }
  html, body { width: 927px; height: 1200px; overflow: hidden; background: var(--paper); }
  .page { position: relative; width: 927px; height: 1200px; background: var(--paper); color: var(--ink); font-family: "Carlito", "Calibri", sans-serif; }

  .top-nav { position: absolute; top: 26px; right: 24px; font-family: "Cinzel", serif; font-size: 12px; letter-spacing: 1.5px; color: var(--caption); white-space: nowrap; }
  .top-nav .sep { margin: 0 10px; }

  .photo-strip { position: absolute; top: 50px; left: 0; width: 927px; height: 135px; }
  .photo { position: absolute; top: 0; height: 135px; }
  .photo--students { left: 0; width: 202px; background: linear-gradient(135deg, var(--photo-campus-b), var(--photo-campus-a)); }
  .photo--skyline { left: 206px; width: 400px; background: linear-gradient(180deg, var(--photo-city-a), var(--photo-city-b)); }
  .photo--street { left: 609px; width: 318px; background: linear-gradient(135deg, var(--photo-street-a), var(--photo-street-b)); }

  .school-title { position: absolute; top: 210px; font-family: "Archivo Black", "Arial Black", sans-serif; font-size: 30px; line-height: 40px; text-align: center; color: var(--ink); }
  .school-title--media { left: 20px; width: 420px; }
  .school-title--letters { left: 470px; width: 425px; }

  .school-body { position: absolute; left: 27px; top: 303px; width: 404px; font-size: 14.2px; line-height: 22px; text-align: justify; }
  .school-body p + p { margin-top: 22px; }

  .courses-title { position: absolute; left: 38px; top: 700px; font-family: "Archivo Black", "Arial Black", sans-serif; font-size: 29px; line-height: 40px; }
  .courses-degree { position: absolute; left: 34px; top: 740px; font-size: 24px; color: var(--muted); }
  .majors { position: absolute; left: 56px; top: 778px; list-style: none; font-size: 18.5px; color: var(--muted); }
  .majors li { position: relative; padding-left: 27px; height: 33px; line-height: 26px; }
  .majors li::before { content: ""; position: absolute; left: 4px; top: 11px; width: 5px; height: 5px; border-radius: 50%; background: var(--ink); }
  .dagger { color: var(--dagger); font-size: 16px; }

  .footnote { position: absolute; font-family: "Cinzel", serif; font-size: 12px; letter-spacing: 0.6px; color: var(--caption); }
  .footnote .dagger { margin-right: 10px; }
  .footnote--one { left: 70px; top: 925px; }
  .footnote--two { left: 55px; top: 963px; }

  .footer-rule { position: absolute; left: 0; top: 1146px; width: 927px; height: 2px; background: var(--rule); }
  .footer-brand { position: absolute; right: 24px; top: 1100px; display: flex; align-items: center; gap: 8px; font-size: 17px; font-weight: 700; color: var(--brand); }
  .footer-brand .dot { width: 18px; height: 18px; border-radius: 50%; background: var(--brand); }
  .folio { position: absolute; right: 91px; top: 1167px; font-size: 12.5px; letter-spacing: 0.3px; color: var(--muted); }
</style>
</head>
<body>
<div class="page">
  <nav class="top-nav">SAMPLE TEXT<span class="sep">|</span>Text Text<span class="sep">|</span>sample.sample</nav>

  <div class="photo-strip">
    <div class="photo photo--students" role="img" aria-label="Photo of students relaxing on a campus lawn"></div>
    <div class="photo photo--skyline" role="img" aria-label="Photo of the downtown city skyline"></div>
    <div class="photo photo--street" role="img" aria-label="Photo of students with bicycles on a city street"></div>
  </div>

  <h1 class="school-title school-title--media">SCHOOL OF MEDIA AND<br>COMMUNICATION</h1>
  <h1 class="school-title school-title--letters">COLLEGE OF LETTERS<br>AND SCIENCES</h1>

  <div class="school-body">
    <p>Text text text text text text, text, sample text, text, sample text, sample text. Sample text, text text text,an Text text text text text text, text, sample text, text, sample text, sample text. Sample text, text text text,an Text text text text text text, text, sample text, text, sample text, sample text.</p>
    <p>Sample text, text text text,an Text text text text text text text, text, sample text, text, sample text, sample text. Sample text, text text text,an text text text text text text, text, sample text, text, sample text, sample text. Sample text, text text text,an Text text text text text text, text, sample text, text, sample text, sample text. Sample text, text text text,an Text text text text text text, text, sample text, text, sample text, sample text. Sample text, text text text,an Text text text text text text text, text.</p>
  </div>

  <h2 class="courses-title">UNDERGRADUATE COURSES</h2>
  <p class="courses-degree">Bachelor of Arts with Majors in</p>
  <ul class="majors">
    <li>Text <span class="dagger">†</span></li>
    <li>Text <span class="dagger">††</span></li>
    <li>Text</li>
  </ul>

  <p class="footnote footnote--one"><span class="dagger">†</span>Sample text</p>
  <p class="footnote footnote--two"><span class="dagger">††</span>Sample text</p>

  <div class="footer-brand"><span class="dot"></span>Redwell Institute</div>
  <div class="footer-rule"></div>
  <p class="folio">2:: REDWELL INSTITUTE</p>
</div>
</body>
</html>
```